Wedding Invitation for a wedding at home - personal, romantic event

Want a wedding invitation that is to be printed onto card.
Size to be 148mm x 210mm
For it to open like a book not tent card
Have a picture of a house that I want to be the front cover.
I've attached 2 pictures. I like the picture without the man but with the grass
For the photo to become a drawing and the colours to be brighter.
If you could use the picture of us and get us in one of the windows.
If you could put the picture of the dog maybe somewhere on the grass.
Love the colour of the sky in the picture of the beach

Words to be on the inside of the card:
Together with our families
You are invited to the Wedding Reception of Tessa Pimble and Roy Fenwick
On Saturday 9th of September 2017 at 6pm
At Fenwick's Keep, 41b, Marrow Crescent, Camberley, Surrey, RH19 4PW
Carriages at 1am
RSVP by Friday 27th of July to 07713 586 201

Words on the Back page:
With all that we have, we've been truly blessed.
Your presence and prayers are all that we request.
But if you desire to give nonetheless,
Monetary gift is one we suggest.

If the pages can be white.
Writing in gold
gold border on all pages

Target Market(s)

Wedding guests

Industry/Entity Type

Wedding

Font styles to use
Script

Requirements
Must have
• Romantic feel. Our wedding colours are white, gold and rose gold.
• Designer to be creative and I do not have much inspiration.
Nice to have
• metallic colours
• Maybe have MR & MRS in gold metallic on the front page

```html
<!DOCTYPE html>
<html lang="en">
<head>
<meta charset="utf-8">
<title>Wedding Card – Back Page Options</title>
<link rel="stylesheet" href="https://fonts.googleapis.com/css2?family=Cormorant+Garamond:wght@500&family=Great+Vibes&family=Lato:wght@400&display=swap">
<style>
  :root {
    --board-light: #b4b4b4;
    --board-mid: #6a6a6a;
    --board-dark: #363636;
    --label: #ffffff;
    --paper: #ffffff;
    --gold: #8b5a10;
    --gold-light: #c4913a;
    --gold-deep: #7a4e08;
    --shadow: rgba(0, 0, 0, 0.45);
  }

  * { box-sizing: border-box; margin: 0; padding: 0; }

  html, body {
    width: 1200px;
    height: 752px;
    overflow: hidden;
  }

  .board {
    position: relative;
    width: 1200px;
    height: 752px;
    background: linear-gradient(200deg, var(--board-light) 0%, var(--board-mid) 45%, var(--board-dark) 100%);
    font-family: "Lato", "Helvetica Neue", Arial, sans-serif;
  }

  .option-label {
    position: absolute;
    color: var(--label);
    font-size: 35.5px;
    font-weight: 400;
    letter-spacing: 0.6px;
    line-height: 1;
    white-space: nowrap;
  }
  .option-label--vertical { left: 106px; top: 45px; }
  .option-label--horizontal { left: 676px; top: 180px; }

  .card {
    position: absolute;
    background: var(--paper);
    box-shadow: 0 6px 24px var(--shadow);
  }
  .card--vertical { left: 55px; top: 120px; width: 425px; height: 602px; }
  .card--horizontal { left: 544px; top: 272px; width: 602px; height: 425px; }

  .card__border {
    position: absolute;
    inset: 25px;
    border: 2px solid var(--gold);
    border-image: linear-gradient(135deg, var(--gold-light), var(--gold-deep) 50%, var(--gold-light)) 1;
  }

  .verse {
    position: absolute;
    left: 0;
    right: 0;
    text-align: center;
    color: var(--gold);
    font-family: "Cormorant Garamond", Georgia, serif;
    font-weight: 500;
    transform: translateY(-50%);
  }
  .verse__line { display: block; white-space: nowrap; }
  .verse__initial {
    font-family: "Great Vibes", cursive;
    font-weight: 400;
    line-height: 0;
    vertical-align: -0.05em;
  }

  .card--vertical .verse {
    top: 46.3%;
    font-size: 15.5px;
    line-height: 22px;
  }
  .card--vertical .verse__initial { font-size: 36px; }

  .card--horizontal .verse {
    top: 47.5%;
    font-size: 21.5px;
    line-height: 30.5px;
  }
  .card--horizontal .verse__initial { font-size: 50px; }
</style>
</head>
<body>
  <main class="board">
    <h2 class="option-label option-label--vertical">OPTION-1 (Vertical)</h2>
    <section class="card card--vertical" aria-label="Back page, vertical layout">
      <div class="card__border"></div>
      <p class="verse">
        <span class="verse__line"><span class="verse__initial">W</span>ith all that we have, we've been truly blessed.</span>
        <span class="verse__line">Your presence and prayers are all that we request.</span>
        <span class="verse__line">But if you desire to give nonetheless,</span>
        <span class="verse__line">Monetary gift is one we suggest.</span>
      </p>
    </section>

    <h2 class="option-label option-label--horizontal">OPTION-2 (Horizontal)</h2>
    <section class="card card--horizontal" aria-label="Back page, horizontal layout">
      <div class="card__border"></div>
      <p class="verse">
        <span class="verse__line"><span class="verse__initial">W</span>ith all that we have, we've been truly blessed.</span>
        <span class="verse__line">Your presence and prayers are all that we request.</span>
        <span class="verse__line">But if you desire to give nonetheless,</span>
        <span class="verse__line">Monetary gift is one we suggest.</span>
      </p>
    </section>
  </main>
</body>
</html>
```